body balm label design

body balm tube design, current label design for other similar products
Need to have a design which can interchange between 3 different solutions
Amber Tide (Lavender + Vanilla)
Copper Ridge (Eucalyptus + Mint)
Fern Hollow (Bergamot + Cedarwood)
Tube size:
2.5h x 3.25 w
Target Market(s)
natural, solution focused
Requirements
Must have
- relatable to existing brand designs, focus on features and benefits

```html
<!DOCTYPE html>
<html lang="en">
<head>
<meta charset="utf-8">
<title>Amber Tide Natural Body Balm Label</title>
<link href="https://fonts.googleapis.com/css2?family=Playfair+Display:wght@400&family=Montserrat:wght@300;400;600&family=Allison&family=Cormorant+Garamond:wght@500&display=swap" rel="stylesheet">
<style>
  :root {
    --canvas-bg: #eef0f4;
    --label-bg: #ffffff;
    --slate: #8a9ba5;
    --slate-dark: #6f818c;
    --ink: #7d8e99;
    --line-art: #dde3e7;
    --white: #ffffff;
  }
  * { margin: 0; padding: 0; box-sizing: border-box; }
  html, body {
    width: 960px; height: 1200px; overflow: hidden;
    background: var(--canvas-bg);
  }
  .label-frame {
    position: absolute; left: 40px; top: 277px;
    width: 880px; height: 646px;
  }
  .label {
    position: absolute; left: 0; top: 0;
    width: 770px; height: 565px;
    background: var(--label-bg);
    transform: scale(1.1429);
    transform-origin: 0 0;
    overflow: hidden;
    font-family: "Montserrat", sans-serif;
    color: var(--ink);
  }
  .botanical-art {
    position: absolute; left: 30px; top: 18px;
    width: 300px; height: 515px;
  }
  .guide-line {
    position: absolute; left: 309px; top: 103px;
    width: 2px; height: 462px; background: var(--slate);
  }
  .product-name {
    position: absolute; left: 236px; top: 92px;
    writing-mode: vertical-rl; transform: rotate(180deg);
    font-family: "Playfair Display", serif;
    font-size: 54px; letter-spacing: 6px; line-height: 1;
    color: var(--slate-dark);
  }
  .product-name-script {
    position: absolute; left: 294px; top: 108px;
    writing-mode: vertical-rl; transform: rotate(180deg);
    font-family: "Allison", cursive;
    font-size: 38px; line-height: 1; color: var(--slate-dark);
  }
  .brand-arch {
    position: absolute; left: 335px; top: 93px;
    width: 108px; height: 472px;
    background: var(--slate);
    border-radius: 54px 54px 0 0;
    color: var(--white);
    text-align: center;
  }
  .brand-name {
    margin-top: 20px;
    font-family: "Cormorant Garamond", serif;
    font-size: 11px; letter-spacing: 1.5px;
  }
  .brand-mark {
    display: block; margin: 8px auto 0;
  }
  .product-type {
    position: absolute; top: 165px; left: 0; width: 100%;
    font-weight: 300; font-size: 16px; line-height: 21px; letter-spacing: 0.5px;
  }
  .origin-badge {
    position: absolute; top: 325px; left: 29px;
    width: 50px; height: 50px; border-radius: 50%;
    border: 1.5px solid var(--white);
  }
  .net-weight {
    position: absolute; top: 407px; left: 0; width: 100%;
    font-weight: 300; font-size: 10px; line-height: 13px;
  }
  .scent {
    position: absolute; left: 500px; top: 128px;
    writing-mode: vertical-rl; transform: rotate(180deg);
    font-family: "Allison", cursive;
    font-size: 64px; line-height: 1; color: var(--slate-dark);
    white-space: nowrap;
  }
  .info-column {
    position: absolute; left: 612px; top: 100px; width: 140px;
    font-size: 10px; line-height: 13px; letter-spacing: 0.6px;
    font-weight: 300;
  }
  .info-heading { font-weight: 600; letter-spacing: 0.8px; }
  .usage { margin-top: 40px; }
  .usage .info-heading { margin-bottom: 9px; }
  .social {
    position: absolute; left: 626px; top: 466px;
    display: flex; gap: 12px;
  }
  .social span {
    width: 24px; height: 24px; border-radius: 50%;
    background: var(--slate);
  }
  .maker {
    position: absolute; left: 612px; top: 509px;
    font-size: 10px; font-weight: 300; letter-spacing: 0.6px; line-height: 18px;
  }
  .website { font-weight: 600; }
</style>
</head>
<body>
  <div class="label-frame">
    <div class="label">
      <div class="botanical-art" role="img" aria-label="Faint line illustration of vanilla orchid flowers, buds and leaves"
           style="background: radial-gradient(ellipse at 55% 45%, var(--line-art) 0%, rgba(221,227,231,0.35) 55%, rgba(255,255,255,0) 75%);"></div>

      <div class="guide-line"></div>
      <div class="product-name">AMBER</div>
      <div class="product-name-script">tide</div>

      <div class="brand-arch">
        <div class="brand-name">TERRA BLOOM</div>
        <svg class="brand-mark" width="14" height="14" viewBox="0 0 14 14" aria-hidden="true">
          <circle cx="7" cy="7" r="6" fill="none" stroke="#ffffff" stroke-width="1"/>
        </svg>
        <div class="product-type">NATURAL<br>BODY<br>BALM</div>
        <div class="origin-badge"></div>
        <div class="net-weight">NET WT<br>8 oz<br>/226g</div>
      </div>

      <div class="scent">Lavender + Vanilla</div>

      <div class="info-column">
        <div class="ingredients">
          <div class="info-heading">Ingredients:</div>
          Shea butter, cocoa butter, coconut oil, sweet almond oil, beeswax, lavender essential oil, vanilla extract or vanilla oleoresin, vitamin E oil
        </div>
        <div class="usage">
          <div class="info-heading">How to use:</div>
          Scoop a small amount, warm it between your palms, apply to dry skin areas, gently massage in, let it absorb, use as needed.
        </div>
      </div>

      <div class="social"><span></span><span></span><span></span></div>
      <div class="maker">
        Made by Terra Bloom<br>
        <span class="website">WWW.TERRABLOOM.CA</span>
      </div>
    </div>
  </div>
</body>
</html>
```